The most modern business card ever !!!

Our company call “Vendalo”. Vendalo is a technology company specialized in cruises solutions. Out main product is a platform to reserve cruises. This is a revolutionary platform that make easier to travel agencies and final users to reserve cruises across dozen companies like tibba, wernu, hpv, dgb, etc..We are a “start up”, with a young team of developers and we want to transmit it.. For it, we want something different, a modern business card that represent cruises and technology.. When someone receive this card, this person should say: wowww this is different… this is modern… this is a cruise related company..
- diferent, modern
- traditions business card

```html
<!DOCTYPE html>
<html lang="en">
<head>
<meta charset="utf-8">
<title>Vendalo Business Card</title>
<link href="https://fonts.googleapis.com/css2?family=Open+Sans:wght@400;600;700&display=swap" rel="stylesheet">
<style>
  :root {
    --backdrop: #dcdcdc;
    --card-white: #ffffff;
    --card-blue: #29a8e0;
    --ink: #1a1a1a;
    --ink-soft: #333333;
    --on-blue: #ffffff;
    --rule-on-blue: rgba(255,255,255,0.75);
  }
  * { box-sizing: border-box; margin: 0; padding: 0; }
  html, body {
    width: 1200px; height: 900px; overflow: hidden;
    background: var(--backdrop);
    font-family: "Open Sans", Arial, sans-serif;
  }
  .stage {
    position: relative; width: 1200px; height: 900px;
  }
  .card {
    position: absolute; left: 250px; width: 700px; height: 400px;
    border-radius: 32px;
    box-shadow: 0 6px 18px rgba(0,0,0,0.18);
    overflow: hidden;
  }
  .card--back { top: 40px; background: var(--card-white); color: var(--ink); }
  .card--front { top: 465px; background: var(--card-blue); color: var(--on-blue); }

  .brand {
    font-weight: 600; letter-spacing: 1px; line-height: 1;
  }
  .card--back .brand {
    position: absolute; left: 0; right: 0; top: 135px;
    text-align: center; font-size: 74px; color: var(--ink);
  }
  .address {
    position: absolute; left: 0; right: 0; bottom: 38px;
    text-align: center; font-size: 15px; color: var(--ink-soft); letter-spacing: 0.3px;
  }

  .card--front .brand {
    position: absolute; left: 130px; top: 62px;
    font-size: 92px; color: var(--on-blue);
  }
  .person {
    position: absolute; right: 130px; top: 190px; text-align: right;
  }
  .person__name { font-size: 20px; font-weight: 700; letter-spacing: 0.5px; }
  .person__role { font-size: 16px; font-weight: 400; }
  .rule {
    position: absolute; left: 130px; right: 130px; top: 262px;
    height: 1px; background: var(--rule-on-blue);
  }
  .contacts {
    position: absolute; left: 130px; top: 282px;
    font-size: 16.5px; line-height: 1.7;
  }
  .contacts b { font-weight: 700; }
  .sep { padding: 0 4px; }
</style>
</head>
<body>
<main class="stage">
  <section class="card card--back">
    <div class="brand">Vendalo</div>
    <p class="address">12345, Address Goes Here, Country Name, 123456.</p>
  </section>

  <section class="card card--front">
    <div class="brand">Vendalo</div>
    <div class="person">
      <p class="person__name">MARCUS HALE</p>
      <p class="person__role">Managing Director</p>
    </div>
    <div class="rule"></div>
    <div class="contacts">
      <p><b>P:</b> 044-210 987 654<span class="sep">|</span><b>M:</b> 044-210 987 654</p>
      <p><b>E:</b> hello@vendalo.io<span class="sep">|</span><b>W:</b> www.vendalo.io</p>
    </div>
  </section>
</main>
</body>
</html>
```